Redesign Website - Current one too plain

The description is in the uploaded file. Please let me know if you need any more information. I'd prefer it if someone could implement the design to a WordPress site but the best design will win, regardless.
I would like the forms to look nice as well
UPDATE:
I don't think we can use the images that I provided, I think they make the site look a bit 'cheap' and I really don't know how to replace them. One thought I have had is to make the "Simple, Unique, Effective" a second feature on the right side of the page with the search on the left
Target Market(s)
Small companies, private sellers of cars and people who rent their caravan/holiday home out
Industry/Entity Type
Advertising
Number of Pages Required
3 page
Colors
Designer to choose colors to be used in the design.
Look and feel
Each slider illustrates characteristics of the customer's brand and the style your logo design should communicate.

```html
<!DOCTYPE html>
<html lang="en">
<head>
<meta charset="utf-8">
<title>Kodix — Find a company by its code</title>
<link href="https://fonts.googleapis.com/css2?family=Poppins:wght@400;500;600;700;800&display=swap" rel="stylesheet">
<style>
:root{
  --lime:#e4ff00;
  --ink:#2a2a2a;
  --text:#333333;
  --muted:#e6e6e6;
  --white:#ffffff;
  --line:#dcdcdc;
  --hero-a:#9aa3a8;
  --hero-b:#5f6a5a;
  --hero-c:#3b4046;
}
*{box-sizing:border-box;margin:0;padding:0}
html,body{width:1200px;height:1169px;overflow:hidden;background:var(--white);font-family:"Poppins",sans-serif;color:var(--text)}
.page{position:relative;width:1200px;height:1169px}

.site-header{position:absolute;left:0;top:0;width:1200px;height:87px;background:var(--white)}
.brand{position:absolute;left:89px;top:20px;display:flex;align-items:center;gap:12px}
.brand-dot{width:34px;height:34px;border-radius:50%;background:var(--lime)}
.brand-name{font-size:31px;font-weight:600;letter-spacing:6px;color:var(--ink)}
.main-nav{position:absolute;left:455px;top:23px;height:43px;display:flex;align-items:center}
.nav-item{display:flex;align-items:center;gap:7px;font-size:12.5px;font-weight:500;color:var(--ink);padding:0 22px;height:26px;border-right:1px solid var(--line)}
.nav-item:last-of-type{border-right:none}
.nav-item.is-active{font-weight:700}
.nav-item svg{width:18px;height:18px}
.cta{position:absolute;left:908px;top:23px;width:203px;height:43px;background:var(--lime);border-radius:5px;display:flex;align-items:center;justify-content:center;font-size:12px;font-weight:700;color:var(--ink)}

.hero{position:absolute;left:0;top:87px;width:1200px;height:763px;background:linear-gradient(100deg,var(--hero-b) 0%,var(--hero-a) 35%,#c9ced2 60%,#b8bcc0 80%,var(--hero-c) 100%)}

.search-card{position:absolute;left:89px;top:249px;width:347px;height:380px;background:var(--white);border-radius:24px;border-top:5px solid var(--lime)}
.code{position:absolute;left:92px;top:46px;display:flex;gap:14px}
.code-slot{width:74px;display:flex;flex-direction:column;align-items:center}
.code-char{font-size:132px;font-weight:800;line-height:100px;color:var(--ink);margin:8px 0}
.code-slot svg{width:14px;height:10px}
.type-row{position:absolute;left:29px;top:225px;display:flex;gap:6px}
.type-btn{width:92px;height:36px;background:var(--muted);border-radius:5px;display:flex;align-items:center;justify-content:center;font-size:11.5px;font-weight:600;color:var(--ink)}
.search-btn{position:absolute;left:29px;top:283px;width:288px;height:47px;background:var(--lime);border-radius:5px;border-bottom:2px solid #b9cf00;display:flex;align-items:center;justify-content:center;font-size:11.5px;font-weight:700;color:var(--ink)}

.features{position:absolute;left:222px;top:789px;display:flex;gap:18px}
.feature{width:240px;height:243px;background:var(--white);border-radius:22px;box-shadow:0 18px 40px rgba(0,0,0,.08);text-align:center;padding-top:26px}
.feature svg{width:80px;height:80px}
.feature h3{font-size:22px;font-weight:700;color:var(--ink);margin-top:11px}
.feature p{font-size:13.5px;line-height:18px;margin:12px auto 0;width:190px}

.site-footer{position:absolute;left:89px;top:1105px;width:1022px;border-top:1px solid var(--line);text-align:center;padding-top:20px;font-size:13.5px;font-weight:500;color:var(--ink)}
.to-top{position:absolute;left:1136px;top:1085px;width:40px;height:40px;border-radius:4px;background:var(--ink);display:flex;align-items:center;justify-content:center}
</style>
</head>
<body>
<div class="page">
  <header class="site-header">
    <div class="brand"><span class="brand-dot"></span><span class="brand-name">KODIX</span></div>
    <nav class="main-nav">
      <span class="nav-item is-active"><svg viewBox="0 0 20 20"><path d="M2 10 10 3l8 7h-2v7h-4v-5H8v5H4v-7z" fill="#2a2a2a"/></svg>HOME</span>
      <span class="nav-item"><svg viewBox="0 0 20 20" fill="none" stroke="#2a2a2a" stroke-width="1.4"><rect x="4" y="2" width="13" height="16" rx="1"/><circle cx="10.5" cy="8" r="2.5"/><path d="M6.5 15c1-3 7-3 8 0M2 6h3M2 10h3M2 14h3"/></svg>CONTACT</span>
      <span class="nav-item"><svg viewBox="0 0 20 20" fill="none" stroke="#2a2a2a" stroke-width="1.4"><circle cx="8" cy="6" r="3.5"/><path d="M2 18c0-4 3-6 6-6M11 17l6-6 2 2-6 6h-2z"/></svg>REGISTER</span>
      <span class="nav-item"><svg viewBox="0 0 20 20" fill="none" stroke="#2a2a2a" stroke-width="1.4"><circle cx="10" cy="6" r="4"/><path d="M3 18c0-4 3-6 7-6s7 2 7 6z"/></svg>LOGIN</span>
    </nav>
    <div class="cta">ADVERTISE YOUR COMPANY</div>
  </header>

  <section class="hero" role="img" aria-label="Photo of a white delivery van driving along a city road with tall buildings behind"></section>

  <div class="search-card">
    <div class="code">
      <div class="code-slot">
        <svg viewBox="0 0 14 10"><path d="M2 8 7 3l5 5" fill="none" stroke="#777" stroke-width="1.6"/></svg>
        <span class="code-char">A</span>
        <svg viewBox="0 0 14 10"><path d="M2 2l5 5 5-5" fill="none" stroke="#777" stroke-width="1.6"/></svg>
      </div>
      <div class="code-slot">
        <svg viewBox="0 0 14 10"><path d="M2 8 7 3l5 5" fill="none" stroke="#777" stroke-width="1.6"/></svg>
        <span class="code-char">1</span>
        <svg viewBox="0 0 14 10"><path d="M2 2l5 5 5-5" fill="none" stroke="#777" stroke-width="1.6"/></svg>
      </div>
    </div>
    <div class="type-row">
      <span class="type-btn">CAR</span>
      <span class="type-btn">CARAVAN</span>
      <span class="type-btn">COMPANY</span>
    </div>
    <div class="search-btn">SEARCH</div>
  </div>

  <div class="features">
    <article class="feature">
      <svg viewBox="0 0 80 80" fill="none" stroke="#2a2a2a" stroke-width="2.2" stroke-linecap="round"><path d="M14 70 44 40"/><path d="M47 22l4 8 9 1-7 6 2 9-8-5-8 5 2-9-7-6 9-1z" fill="#e4ff00"/><path d="M47 6v5M66 26h5M62 12l-4 4M30 14l3 4M66 42l-4-3"/></svg>
      <h3>Simple</h3>
      <p>Create your advert and display your code</p>
    </article>
    <article class="feature">
      <svg viewBox="0 0 80 80" fill="none" stroke="#2a2a2a" stroke-width="2.2" stroke-linecap="round"><path d="M14 40a26 26 0 0 1 52 0M20 42a20 20 0 0 1 40 0M26 44a14 14 0 0 1 28 0"/><path d="M36 76V42a4 4 0 0 1 8 0v12l8 2a4 4 0 0 1 3 5l-4 15z" fill="#e4ff00"/></svg>
      <h3>Unique</h3>
      <p>Customers find you by an easy-to-remember code</p>
    </article>
    <article class="feature">
      <svg viewBox="0 0 80 80" fill="none" stroke="#2a2a2a" stroke-width="2.6" stroke-linecap="round"><circle cx="36" cy="46" r="28"/><circle cx="36" cy="46" r="20" fill="#e4ff00"/><circle cx="36" cy="46" r="9"/><path d="M36 46 68 14M62 12l6 2 2 6M66 6v8h8"/></svg>
      <h3>Effective</h3>
      <p>Customers are directed to you and not a list of your competitors</p>
    </article>
  </div>

  <footer class="site-footer">© Copyright 2023 Kodix. All Rights Reserved</footer>
  <div class="to-top"><svg width="10" height="8" viewBox="0 0 10 8"><path d="M2 6 5 3l3 3" fill="none" stroke="#e4ff00" stroke-width="1.6"/></svg></div>
</div>
</body>
</html>
```